Veltrane Group Business Card Design

The CEO is looking for a new trendy look for his business card.
You can stay with current branding or come up with something new/creative. It can be 3D, including Medical Office buildings. You can use our logo in a variety of colors. Please include name, title, company name, company website, email address, cell number

Target Market(s)

Real Estate Development and Construction

Industry/Entity Type

Health care real estate

Contact Information for Business Card

Rohesh Kamdar, CEO M-604.781.2249 E-roheshkamdar@veltrane.com Address:4180 Lindqvist Ave, Tampa, FL 33482 www.veltrane.com

Font styles to use
Other font styles liked:
• Be creative

Requirements
Must have
• Creative, trendy look
Nice to have
• Please go to our website to get a feel- www. veltrane.com
Should not have
• small fonts

```html
<!DOCTYPE html>
<html lang="en">
<head>
<meta charset="utf-8">
<title>Veltrane Group Business Card</title>
<link rel="stylesheet" href="https://fonts.googleapis.com/css2?family=Montserrat:wght@400;600;800&display=swap">
<style>
  :root {
    --backdrop: #e6e6e8;
    --brand-red: #b3202a;
    --brand-red-deep: #8f1820;
    --navy: #1e2b4a;
    --ink: #2b2b2b;
    --paper: #ffffff;
  }
  * { box-sizing: border-box; margin: 0; padding: 0; }
  html, body { width: 1200px; height: 913px; overflow: hidden; }
  body {
    background: var(--backdrop);
    font-family: "Montserrat", Arial, sans-serif;
    position: relative;
  }
  .card {
    position: absolute;
    width: 620px;
    height: 354px;
    border-radius: 22px;
    box-shadow: 0 10px 30px rgba(0,0,0,.18);
    overflow: hidden;
  }
  .card--front {
    left: 150px; top: 60px;
    background: var(--brand-red);
    display: flex; align-items: center; justify-content: center;
  }
  .front-name {
    color: var(--brand-red-deep);
    font-weight: 800;
    font-size: 62px;
    letter-spacing: -1px;
  }
  .card--back {
    left: 430px; top: 499px;
    background: var(--paper);
  }
  .back-logo {
    position: absolute; right: 40px; top: 40px;
    color: var(--brand-red);
    font-weight: 800;
    font-size: 40px;
    letter-spacing: -1px;
  }
  .logo-rule {
    position: absolute; left: 300px; right: 40px; top: 104px;
    height: 2px; background: var(--brand-red);
  }
  .person { position: absolute; left: 40px; top: 150px; }
  .person-name {
    color: var(--brand-red);
    font-weight: 800;
    font-size: 26px;
    letter-spacing: .5px;
  }
  .person-title {
    color: var(--ink);
    font-size: 18px;
    margin-top: 4px;
  }
  .main-rule {
    position: absolute; left: 40px; right: 40px; top: 228px;
    height: 2px; background: var(--brand-red);
  }
  .address {
    position: absolute; right: 40px; top: 244px;
    text-align: right;
    color: var(--ink);
    font-size: 15px;
    line-height: 1.45;
  }
  .contacts {
    position: absolute; left: 40px; top: 244px;
    list-style: none;
    color: var(--ink);
    font-size: 16px;
    line-height: 1.6;
  }
  .contacts li { display: flex; align-items: center; gap: 10px; }
  .contacts svg { width: 14px; height: 14px; flex: none; }
</style>
</head>
<body>
  <section class="card card--front" aria-label="Card front">
    <span class="front-name">Veltrane Group</span>
  </section>

  <section class="card card--back" aria-label="Card back">
    <div class="back-logo">Veltrane Group</div>
    <div class="logo-rule"></div>

    <div class="person">
      <div class="person-name">ROHESH KAMDAR</div>
      <div class="person-title">CEO</div>
    </div>

    <div class="main-rule"></div>

    <ul class="contacts">
      <li>
        <svg viewBox="0 0 14 14"><rect x="3" y="0.8" width="8" height="12.4" rx="1.5" fill="none" stroke="var(--brand-red)" stroke-width="1.6"/><circle cx="7" cy="10.8" r="0.9" fill="var(--brand-red)"/></svg>
        604.781.2249
      </li>
      <li>
        <svg viewBox="0 0 14 14"><rect x="1" y="3" width="12" height="8.5" fill="var(--brand-red)"/><path d="M1 3 L7 8 L13 3" fill="none" stroke="#fff" stroke-width="1.2"/></svg>
        roheshkamdar@veltrane.com
      </li>
      <li>
        <svg viewBox="0 0 14 14"><circle cx="7" cy="7" r="6" fill="var(--brand-red)"/><path d="M1 7 H13 M7 1 C4 4 4 10 7 13 M7 1 C10 4 10 10 7 13" fill="none" stroke="#fff" stroke-width="1"/></svg>
        www.veltrane.com
      </li>
    </ul>

    <address class="address" style="font-style:normal">
      4180 Lindqvist Ave,<br>
      Tampa, FL 33482
    </address>
  </section>
</body>
</html>
```